Personal Development Model Graphic

I am creating a Personal Development/Coaching business and website and need some assistance with the development of a graphic that represents my methodology. I have already done what I consider to be a working version, but now it's time to have a professional design eye take a look at it and improve.

Specifically, I need assistance on color usage. I'd like each of the 8 areas of the model to have a color, and I've tried to utilize colors I feel are representative of the specific area(for example, purple for spirituality) but it doesn't really work for everything and perhaps additional thought could be put to that aspect of it.

Also, the model needs to work in reverse of the way it's pictured in the attached JPEG. So Friends needs to be first (top center)and then going clockwise, Spirituality needs to be in the 1:00 position not the 11:00 position and then continue around to Community, Family, Exercise, Career, Art/Creativity, and last at 11:00 Sexuality. I was going to update it before uploading, but I'm having trouble with Photoshop and just decided to pull the trigger on having a designer do it.

Thank you in advance for your creativity and ideas!

Industry/Entity Type

Business

Requirements
Nice to have
• It would be fantastic if it could feel modern, and high tech. I realize this is difficult with circles! But whatever you can do.

On color usage, it would again be wonderful to have colors that are more modern than traditional. I'll leave that to your discretion.

```html
<!DOCTYPE html>
<html lang="en">
<head>
<meta charset="utf-8">
<title>Happiness Model</title>
<link rel="stylesheet" href="https://fonts.googleapis.com/css2?family=Righteous&display=swap">
<style>
  :root {
    --canvas-bg: #ffffff;
    --label-ink: #2f2d2e;
    --core-ink: #1e1a6b;

    --core-light: #d4e9f7;
    --core-mid: #5aa6da;
    --core-dark: #1f74b8;

    --friends-light: #f9b699;
    --friends-dark: #ee5526;
    --spirit-light: #d9c3e6;
    --spirit-dark: #5e2590;
    --community-light: #e6dbcf;
    --community-dark: #5a3618;
    --family-light: #d2e5d8;
    --family-dark: #1a653a;
    --exercise-light: #fffbd6;
    --exercise-dark: #f7e01c;
    --career-light: #d6d6ee;
    --career-dark: #2a2883;
    --art-light: #f8b9d5;
    --art-dark: #e5177a;
    --sexuality-light: #f1c1c3;
    --sexuality-dark: #b22b35;
  }
  html, body {
    margin: 0;
    padding: 0;
    overflow: hidden;
    background: var(--canvas-bg);
  }
  .model {
    display: block;
    width: 1200px;
    height: 1000px;
  }
  .area-label {
    font-family: "Righteous", sans-serif;
    font-size: 25px;
    letter-spacing: 1.5px;
    fill: var(--label-ink);
    text-anchor: middle;
    dominant-baseline: central;
  }
  .core-label {
    font-family: "Righteous", sans-serif;
    font-size: 64px;
    letter-spacing: 2px;
    fill: var(--core-ink);
    text-anchor: middle;
    dominant-baseline: central;
  }
  .connector { opacity: 0.9; }
</style>
</head>
<body>
<svg class="model" viewBox="0 0 1200 1000" xmlns="http://www.w3.org/2000/svg" role="img" aria-label="Happiness at the centre, surrounded by eight life areas">
  <defs>
    <radialGradient id="grad-core" cx="0.25" cy="0.2" r="0.95">
      <stop offset="0" style="stop-color: var(--core-light)"/>
      <stop offset="0.45" style="stop-color: var(--core-mid)"/>
      <stop offset="1" style="stop-color: var(--core-dark)"/>
    </radialGradient>
    <radialGradient id="grad-friends" cx="0.2" cy="0.2" r="0.95">
      <stop offset="0" style="stop-color: var(--friends-light)"/>
      <stop offset="1" style="stop-color: var(--friends-dark)"/>
    </radialGradient>
    <radialGradient id="grad-spirit" cx="0.2" cy="0.2" r="0.95">
      <stop offset="0" style="stop-color: var(--spirit-light)"/>
      <stop offset="1" style="stop-color: var(--spirit-dark)"/>
    </radialGradient>
    <radialGradient id="grad-community" cx="0.2" cy="0.2" r="0.95">
      <stop offset="0" style="stop-color: var(--community-light)"/>
      <stop offset="1" style="stop-color: var(--community-dark)"/>
    </radialGradient>
    <radialGradient id="grad-family" cx="0.2" cy="0.2" r="0.95">
      <stop offset="0" style="stop-color: var(--family-light)"/>
      <stop offset="1" style="stop-color: var(--family-dark)"/>
    </radialGradient>
    <radialGradient id="grad-exercise" cx="0.2" cy="0.2" r="0.95">
      <stop offset="0" style="stop-color: var(--exercise-light)"/>
      <stop offset="1" style="stop-color: var(--exercise-dark)"/>
    </radialGradient>
    <radialGradient id="grad-career" cx="0.2" cy="0.2" r="0.95">
      <stop offset="0" style="stop-color: var(--career-light)"/>
      <stop offset="1" style="stop-color: var(--career-dark)"/>
    </radialGradient>
    <radialGradient id="grad-art" cx="0.2" cy="0.2" r="0.95">
      <stop offset="0" style="stop-color: var(--art-light)"/>
      <stop offset="1" style="stop-color: var(--art-dark)"/>
    </radialGradient>
    <radialGradient id="grad-sexuality" cx="0.2" cy="0.2" r="0.95">
      <stop offset="0" style="stop-color: var(--sexuality-light)"/>
      <stop offset="1" style="stop-color: var(--sexuality-dark)"/>
    </radialGradient>
    <polygon id="connector-shape" points="-30,-190 30,-190 64,-300 -64,-300"/>
  </defs>

  <g class="connectors" transform="translate(598 497)">
    <use class="connector" href="#connector-shape" fill="var(--friends-dark)" transform="rotate(0)"/>
    <use class="connector" href="#connector-shape" fill="var(--spirit-dark)" transform="rotate(45)"/>
    <use class="connector" href="#connector-shape" fill="var(--community-dark)" transform="rotate(90)"/>
    <use class="connector" href="#connector-shape" fill="var(--family-dark)" transform="rotate(135)"/>
    <use class="connector" href="#connector-shape" fill="var(--exercise-dark)" transform="rotate(180)"/>
    <use class="connector" href="#connector-shape" fill="var(--career-dark)" transform="rotate(225)"/>
    <use class="connector" href="#connector-shape" fill="var(--art-dark)" transform="rotate(270)"/>
    <use class="connector" href="#connector-shape" fill="var(--sexuality-dark)" transform="rotate(315)"/>
  </g>

  <g class="area area-friends">
    <circle cx="598" cy="124" r="108" fill="url(#grad-friends)"/>
    <text class="area-label" x="598" y="124">FRIENDS</text>
  </g>
  <g class="area area-spirituality">
    <circle cx="860" cy="233" r="108" fill="url(#grad-spirit)"/>
    <text class="area-label" x="860" y="233">SPIRITUALITY</text>
  </g>
  <g class="area area-community">
    <circle cx="970" cy="495" r="108" fill="url(#grad-community)"/>
    <text class="area-label" x="970" y="495">COMMUNITY</text>
  </g>
  <g class="area area-family">
    <circle cx="860" cy="758" r="108" fill="url(#grad-family)"/>
    <text class="area-label" x="860" y="758">FAMILY</text>
  </g>
  <g class="area area-exercise">
    <circle cx="598" cy="866" r="108" fill="url(#grad-exercise)"/>
    <text class="area-label" x="598" y="866">EXERCISE</text>
  </g>
  <g class="area area-career">
    <circle cx="337" cy="758" r="108" fill="url(#grad-career)"/>
    <text class="area-label" x="337" y="758">CAREER</text>
  </g>
  <g class="area area-art">
    <circle cx="227" cy="495" r="108" fill="url(#grad-art)"/>
    <text class="area-label" x="227" y="478">ART</text>
    <text class="area-label" x="227" y="512">CREATIVITY</text>
  </g>
  <g class="area area-sexuality">
    <circle cx="337" cy="233" r="108" fill="url(#grad-sexuality)"/>
    <text class="area-label" x="337" y="233">SEXUALITY</text>
  </g>

  <g class="core">
    <circle cx="598" cy="492" r="197" fill="url(#grad-core)"/>
    <text class="core-label" x="598" y="492">HAPPINESS</text>
  </g>
</svg>
</body>
</html>
```